Fresh, modern, fun business card for pediatric dental practice

Need a business card for fresh, modern, fun pediatric dental practice

Clean look that matches our website's font and colors

We prefer the look of curved corners on business cards

Target Market(s)

parents (mothers) of young children, professionals, mid-high class

Industry/Entity Type

Dental

Contact Information for Business Card

Maplebrook Pediatric Dentistry
482 Quarry Lane
Suite 517
Fernwick, PA 17088
717.555.0193
www.maplebrookkidsdental.example

Mei-Ran Tsai, DMD
Corinne Walbeck, DMD
(we are working on our email address, but we would like that on the card as well)

Font styles to use
Sans Serif

Requirements
Must have
• All info; we would also like to make cards for individual staff members
• colors from our website and color palatte, attatched
• use same font and design as website for branding
Nice to have
• clean, simple card that has a pop of color
• we would like to see a few designs with our tag line "where little smiles grow"
• we are not sure if we want to have it on there or not
• we would like to see a few designs incorporating the ribbon graphic on our website where the word WELCOME is

```html
<!DOCTYPE html>
<html lang="en">
<head>
<meta charset="utf-8">
<title>Maplebrook Pediatric Dentistry – Business Card</title>
<link rel="stylesheet" href="https://fonts.googleapis.com/css2?family=Lato:wght@400;700&family=Roboto:wght@500;700&display=swap">
<style>
  :root {
    --plum: #5a2b5a;
    --plum-deep: #43193f;
    --magenta: #c8268f;
    --gold: #e9a81f;
    --ink: #4a4a4a;
    --paper: #ffffff;
    --backdrop: #9a9a9a;
    --front-text: #ece6ee;
  }
  * { box-sizing: border-box; margin: 0; padding: 0; }
  html, body { width: 1200px; height: 900px; overflow: hidden; }
  body {
    background: var(--backdrop);
    font-family: "Lato", sans-serif;
    position: relative;
  }
  .card {
    position: absolute;
    width: 560px;
    height: 320px;
    border-radius: 22px;
    overflow: hidden;
    box-shadow: 0 10px 24px rgba(0,0,0,0.25);
  }

  /* Front */
  .card-front {
    left: 60px; top: 90px;
    background: radial-gradient(circle at 60% 60%, #653565 0%, var(--plum) 55%, #4c224a 100%);
    display: flex; align-items: center; justify-content: center;
  }
  .brand { display: flex; align-items: center; gap: 14px; }
  .brand-dot { width: 22px; height: 22px; border-radius: 50%; flex: none; }
  .brand-name {
    font-family: "Lato", sans-serif;
    font-weight: 700;
    line-height: 1.1;
  }
  .brand-name span { display: block; }
  .card-front .brand-dot { background: var(--front-text); }
  .card-front .brand-name { color: var(--front-text); font-size: 34px; }
  .card-front .brand-name span { font-size: 22px; }

  /* Back */
  .card-back { left: 580px; top: 490px; background: var(--paper); }
  .back-logo { position: absolute; left: 30px; top: 95px; width: 230px; }
  .card-back .brand-dot { background: var(--gold); }
  .card-back .brand-name { color: var(--gold); font-size: 28px; }
  .card-back .brand-name span { font-size: 18px; }
  .divider {
    position: absolute; left: 272px; top: 40px;
    width: 2px; height: 180px;
    background: var(--plum);
  }
  .details {
    position: absolute; left: 292px; top: 36px; right: 14px;
    color: var(--ink);
  }
  .doctor {
    font-family: "Roboto", sans-serif;
    font-weight: 700;
    font-size: 18px;
    color: var(--magenta);
    line-height: 1.3;
    white-space: nowrap;
  }
  .doctor .credential { color: var(--gold); font-weight: 500; }
  .address { margin-top: 12px; font-size: 12.5px; line-height: 1.4; }
  .contact-list { list-style: none; margin-top: 12px; }
  .contact-list li {
    display: flex; align-items: center; gap: 8px;
    font-size: 12.5px; line-height: 1; margin-bottom: 6px;
    white-space: nowrap;
  }
  .contact-list svg { width: 16px; height: 16px; flex: none; }
  .tagline-band {
    position: absolute; left: 0; right: 0; top: 238px; height: 56px;
    background: var(--plum-deep);
    display: flex; align-items: center; justify-content: flex-end;
    padding-right: 70px;
  }
  .tagline { color: #f2eaf2; font-size: 15px; letter-spacing: 0.2px; }
</style>
</head>
<body>
  <section class="card card-front" aria-label="Card front">
    <div class="brand">
      <span class="brand-dot"></span>
      <p class="brand-name">Maplebrook<span>Pediatric Dentistry</span></p>
    </div>
  </section>

  <section class="card card-back" aria-label="Card back">
    <div class="back-logo brand">
      <span class="brand-dot"></span>
      <p class="brand-name">Maplebrook<span>Pediatric Dentistry</span></p>
    </div>
    <div class="divider"></div>
    <div class="details">
      <p class="doctor">Mei-Ran Tsai, <span class="credential">DMD</span></p>
      <p class="doctor">Corinne Walbeck, <span class="credential">DMD</span></p>
      <p class="address">482 Quarry Lane, Suite 517<br>Fernwick, PA 17088</p>
      <ul class="contact-list">
        <li>
          <svg viewBox="0 0 16 16" aria-hidden="true"><circle cx="8" cy="8" r="8" fill="var(--plum)"/><path d="M5.3 4.2l1.3 1.6-.7.9c.5 1.1 1.3 1.9 2.4 2.4l.9-.7 1.6 1.3-.6 1.4c-2.9-.2-5.2-2.5-5.4-5.4z" fill="#fff"/></svg>
          717.555.0193
        </li>
        <li>
          <svg viewBox="0 0 16 16" aria-hidden="true"><circle cx="8" cy="8" r="8" fill="var(--plum)"/><rect x="4" y="5.2" width="8" height="5.6" rx="0.6" fill="#fff"/><path d="M4.3 5.6L8 8.4l3.7-2.8" stroke="var(--plum)" stroke-width="0.9" fill="none"/></svg>
          info@maplebrookkidsdental.example
        </li>
        <li>
          <svg viewBox="0 0 16 16" aria-hidden="true"><circle cx="8" cy="8" r="8" fill="var(--plum)"/><circle cx="8" cy="8" r="4" stroke="#fff" stroke-width="1" fill="none"/><path d="M4 8h8M8 4c-1.6 2.4-1.6 5.6 0 8M8 4c1.6 2.4 1.6 5.6 0 8" stroke="#fff" stroke-width="0.8" fill="none"/></svg>
          www.maplebrookkidsdental.example
        </li>
      </ul>
    </div>
    <div class="tagline-band">
      <p class="tagline">where little smiles grow</p>
    </div>
  </section>
</body>
</html>
```